Lumvra App | Pre-Launch Homepage

Dear designer,
Lumvra is a soon to be launched innovative & free social platform for collaborative addictions quitting.
We require a design for our pre-launch homepage that will elevate our basic wireframes to the next level.
We would like the wireframes to serve as a guideline only, and not as a final version of the design. If you have cool ideas - we would appreciate your creativity!
* This is a pre-launch website for a mobile app, and as such the design must be consistent with the general style, design and atmosphere of the app (see screenshot in the shared Drive link).
* We liked the style and feel of the following website: http://tandelhub.example/ - Please let's use it as a reference as well.
* The existing text in the wireframes is there just to represent a place for text. Copy will be edited by us after the design is done.
Please find the wireframes attached, and all relevant design assets and app screenshots in the following Drive shared link -
https://files.example-share.net/open?id=7KQ204RtP3mNxa8Y2Lb61H9cdVzQ
Thanks,
Reginald
Industry/Entity Type
Social
Number of Pages Required
1 page
Look and feel
Each slider illustrates characteristics of the customer's brand and the style your logo design should communicate.

```html
<!DOCTYPE html>
<html lang="en">
<head>
<meta charset="utf-8">
<title>Lumvra App | Pre-Launch Homepage</title>
<link href="https://fonts.googleapis.com/css2?family=Open+Sans:wght@400;600;700&family=Raleway:wght@200;300;400;600;700&display=swap" rel="stylesheet">
<style>
:root{
  --orange:#f7931e;
  --orange-deep:#f07a12;
  --yellow:#fbb829;
  --yellow-soft:#fdd060;
  --ink:#333333;
  --grey:#8c8c8c;
  --dark:#2c2c2c;
  --charcoal:#3b3b3b;
  --blue:#1fb0e6;
  --white:#ffffff;
}
*{margin:0;padding:0;box-sizing:border-box}
html,body{width:1200px;height:4024px;overflow:hidden}
body{font-family:'Open Sans',sans-serif;color:var(--ink);background:var(--white);position:relative}
section,header,footer{position:absolute;left:0;width:1200px;overflow:hidden}
.abs{position:absolute}
.thin{font-family:'Raleway',sans-serif;font-weight:200}
.brand{font-family:'Raleway',sans-serif;font-weight:700;color:var(--yellow);font-size:44px;letter-spacing:1px}
.device{position:absolute;border-radius:28px}

/* hero */
.hero{top:0;height:720px}
.hero-bg{position:absolute;inset:0;background:linear-gradient(155deg,#7d7c74 0%,#9d9382 22%,#d39a45 45%,#f6a327 62%,var(--orange) 100%)}
.hero .brand{left:70px;top:38px}
.contact-btn{left:920px;top:40px;width:120px;height:38px;border:2px solid var(--yellow);color:var(--yellow);font-size:14px;font-weight:600;display:flex;align-items:center;justify-content:center;border-radius:3px}
.contact-dot{left:1060px;top:40px;width:38px;height:38px;border-radius:50%;background:var(--yellow)}
.hero h1{left:70px;top:220px;width:340px;color:var(--white);font-family:'Raleway',sans-serif;font-weight:400;font-size:34px;line-height:42px}
.hero .lead{left:70px;top:320px;width:300px;color:var(--white);font-size:18px;line-height:27px}
.hero .lead b{color:var(--yellow)}
.hero .phone{left:430px;top:40px;width:300px;height:420px;transform:rotate(-16deg);background:linear-gradient(160deg,#e9e9e9,#b9b9b9 8%,#323846 14%,#465066 60%,#2a2f3a 88%,#dedede 94%)}
.hero .sub-note{left:700px;top:172px;width:420px;color:var(--white);font-size:15px}
.hero .email{left:700px;top:212px;width:420px;height:44px;border:1px solid rgba(255,255,255,.8);border-radius:3px;display:flex;align-items:center;padding-left:16px;color:var(--white);font-size:14px}
.hero .email span.go{position:absolute;right:0;top:0;width:56px;height:42px;background:var(--orange);display:flex;align-items:center;justify-content:center}

/* features */
.features{top:700px;height:260px}
.feature{position:absolute;width:260px;text-align:center}
.feature .ring{width:110px;height:110px;margin:0 auto;border-radius:50%;background:#c9c9c9;border:6px solid #e6e6e6;display:flex;align-items:center;justify-content:center}
.feature .ring svg{width:64px;height:64px}
.feature h3{font-family:'Raleway',sans-serif;font-size:18px;font-weight:600;color:var(--ink);margin-top:14px}
.feature p{font-size:12px;color:var(--grey);line-height:17px;margin-top:4px}

/* fun */
.fun{top:930px;height:420px}
.fun h2{left:80px;top:80px;font-size:66px;color:var(--white)}
.fun .rule{left:80px;top:160px;width:90px;height:2px;background:var(--white)}
.fun p{left:80px;width:470px;color:var(--white);font-size:14px;line-height:21px}
.fun p b{color:var(--yellow-soft)}
.fun .tablet{left:660px;top:40px;width:420px;height:300px;transform:rotate(-12deg);border-radius:22px;background:linear-gradient(150deg,#f3f3f3,#d6d6d6 6%,#3a3f4d 10%,#505c70 55%,#2a2e38 90%,#e8e8e8 95%)}

/* inspire */
.inspire{top:1350px;height:400px}
.inspire .tablet{left:170px;top:40px;width:400px;height:290px;transform:rotate(8deg);border-radius:22px;background:linear-gradient(150deg,#f4f4f4,#d9d9d9 6%,#5b4f46 10%,#a06d44 45%,#3d3a3a 90%,#eaeaea 95%)}
.inspire h2{left:650px;top:60px;font-size:62px;color:var(--white)}
.inspire .rule{left:650px;top:140px;width:90px;height:2px;background:var(--white)}
.inspire p{left:650px;width:420px;font-size:15px;line-height:23px;color:var(--ink)}
.inspire p b{color:var(--white)}

/* achieve */
.achieve{top:1780px;height:600px}
.achieve h2{left:0;width:1200px;top:40px;text-align:center;font-size:56px;color:var(--orange);font-weight:300}
.achieve .rule{left:560px;top:118px;width:80px;height:2px;background:var(--orange)}
.achieve .intro{left:300px;width:600px;text-align:center;font-size:15px;line-height:23px;color:var(--grey)}
.achieve .intro b{color:var(--ink)}
.achieve .phone{left:470px;top:220px;width:260px;height:380px;border-radius:34px;background:linear-gradient(180deg,#1c1c1c 0%,#1c1c1c 10%,#4a3d35 14%,#6a5b4c 50%,#2d2d33 86%,#1c1c1c 90%)}
.point{position:absolute;display:flex;align-items:center;gap:22px;width:380px}
.point p{font-size:13px;line-height:19px;color:var(--grey);width:260px}
.point .dot{width:64px;height:64px;border-radius:50%;background:#9a9a9a;border:5px solid #dcdcdc;flex:none;display:flex;align-items:center;justify-content:center}
.point.right p{order:2}

/* coming soon */
.soon{top:2380px;height:600px}
.soon-bg{position:absolute;inset:0;background:linear-gradient(180deg,#6a5a48 0%,#4a3f34 40%,#262626 100%)}
.soon h2{left:0;width:1200px;top:60px;text-align:center;color:var(--white);font-family:'Raleway',sans-serif;font-weight:400;font-size:44px}
.soon .phone{left:470px;top:130px;width:260px;height:440px;border-radius:36px;background:linear-gradient(180deg,#f2f2f2 0%,#d4d4d4 8%,#3a3a44 14%,#55506a 55%,#2b2b35 84%,#d8d8d8 90%,#eeeeee 100%)}

/* stores */
.stores{top:2980px;height:140px;display:flex}
.store{width:400px;height:140px;display:flex;flex-direction:column;align-items:center;justify-content:center;color:var(--white);text-align:center}
.store .mark{width:34px;height:34px;border-radius:50%;background:var(--white);opacity:.9;margin-bottom:10px}
.store small{font-size:12px}
.store strong{font-size:18px;font-weight:700;letter-spacing:.5px}
.store.s1{background:var(--charcoal)}
.store.s2{background:var(--yellow)}
.store.s3{background:var(--blue)}

/* desktop */
.desktop{top:3120px;height:400px;background:var(--charcoal)}
.desktop .ghost{left:440px;top:40px;font-family:'Raleway',sans-serif;font-weight:700;font-size:150px;color:rgba(255,255,255,.05);letter-spacing:4px}
.desktop h2{left:80px;top:60px;width:560px;font-size:24px;line-height:32px;color:var(--white);font-weight:700;text-transform:uppercase}
.desktop p{left:80px;top:150px;width:520px;font-size:14px;line-height:22px;color:#d0d0d0}
.desktop .icons{left:80px;top:280px;display:flex;gap:16px}
.desktop .icons span{width:40px;height:40px;border-radius:50%;border:2px solid #bdbdbd}
.desktop .devices{left:640px;top:70px;width:500px;height:290px;border-radius:6px;background:linear-gradient(135deg,#d8d8d8,#8a8a8a 20%,#3f4654 40%,#5b6578 70%,#c9c9c9 100%)}

/* photo strip */
.strip{top:3520px;height:180px;display:flex}
.strip div{width:200px;height:180px}

/* footer */
.site-footer{top:3700px;height:324px;background:var(--orange)}
.site-footer h2{left:80px;top:36px;color:var(--white);font-size:22px;font-weight:700}
.site-footer .email{left:80px;top:86px;width:400px;height:44px;background:rgba(255,255,255,.15);border:1px solid rgba(255,255,255,.7);border-radius:3px;display:flex;align-items:center;padding-left:16px;color:var(--white);font-size:14px}
.site-footer .email .go{position:absolute;right:0;top:0;width:56px;height:42px;background:var(--yellow);display:flex;align-items:center;justify-content:center}
.site-footer .brand{left:80px;top:160px;color:var(--white);font-size:40px}
.counts{left:260px;top:168px;display:flex;gap:12px}
.counts span{display:flex;align-items:center;gap:8px;background:var(--white);color:var(--orange);font-weight:700;font-size:13px;padding:6px 14px 6px 8px;border-radius:16px}
.counts i{width:16px;height:16px;border-radius:50%;background:var(--orange);display:block}
.legal{left:80px;top:240px;color:var(--white);font-size:13px}
.legal span{margin-right:14px}
.copyright{left:80px;top:276px;color:rgba(255,255,255,.85);font-size:12px}
.footer-stores{left:720px;top:0;width:480px}
.footer-stores div{height:108px;display:flex;align-items:center;gap:16px;padding-left:150px;color:var(--white)}
.footer-stores .mark{width:30px;height:30px;border-radius:50%;background:var(--white)}
.footer-stores small{display:block;font-size:11px}
.footer-stores strong{font-size:16px}
</style>
</head>
<body>

<header class="hero">
  <div class="hero-bg" role="img" aria-label="Weathered grey wood texture fading into a warm orange and yellow wash"></div>
  <svg class="abs" style="left:0;top:0" width="1200" height="720" viewBox="0 0 1200 720" aria-hidden="true">
    <polygon points="0,560 600,720 1200,560 1200,720 0,720" fill="#ffffff"/>
  </svg>
  <div class="abs brand">Lumvra</div>
  <div class="abs contact-btn">Contact Us</div>
  <div class="abs contact-dot"></div>
  <h1 class="abs">Become a Better Version of Yourself</h1>
  <p class="abs lead">Lumvra is a revolutionary &amp; <b>free</b> social platform for collaborative addictions quitting.</p>
  <div class="device phone" role="img" aria-label="Smartphone showing the Lumvra app home screen"></div>
  <p class="abs sub-note">Subscribe below for the beta release and updates</p>
  <div class="abs email">Enter your e-mail address
    <span class="go"><svg width="20" height="14" viewBox="0 0 20 14"><rect x="1" y="1" width="18" height="12" fill="none" stroke="#fff" stroke-width="2"/><polyline points="1,1 10,8 19,1" fill="none" stroke="#fff" stroke-width="2"/></svg></span>
  </div>
</header>

<section class="features">
  <div class="feature" style="left:130px;top:0">
    <div class="ring"><svg viewBox="0 0 64 64"><circle cx="32" cy="32" r="26" fill="#e53b2c"/><circle cx="32" cy="32" r="13" fill="#fff"/><g stroke="#fff" stroke-width="9"><line x1="32" y1="6" x2="32" y2="19"/><line x1="32" y1="45" x2="32" y2="58"/><line x1="6" y1="32" x2="19" y2="32"/><line x1="45" y1="32" x2="58" y2="32"/></g></svg></div>
    <h3>Never be Alone</h3>
    <p>Forget what you know - Lumvra<br>makes it fun to quit</p>
  </div>
  <div class="feature" style="left:470px;top:60px">
    <div class="ring"><svg viewBox="0 0 64 64"><polygon points="32,4 40,24 61,24 44,37 50,58 32,45 14,58 20,37 3,24 24,24" fill="#f4b400"/></svg></div>
    <h3>Network Power</h3>
    <p>Forget what you know - Lumvra<br>makes it fun to quit</p>
  </div>
  <div class="feature" style="left:810px;top:0">
    <div class="ring"><svg viewBox="0 0 64 64" fill="none" stroke="#555" stroke-width="2.5"><path d="M18 48 C14 38 14 26 22 18 C30 10 44 12 48 24"/><path d="M24 52 C20 42 20 30 28 24 C36 20 42 26 42 34"/><path d="M32 54 C28 46 28 36 32 32 C36 30 36 38 36 42"/><path d="M40 52 C44 44 48 36 48 30"/></svg></div>
    <h3>Stay Motivated</h3>
    <p>Forget what you know - Lumvra<br>makes it fun to quit</p>
  </div>
</section>

<section class="fun">
  <svg class="abs" style="left:0;top:0" width="1200" height="420" viewBox="0 0 1200 420" aria-hidden="true">
    <polygon points="0,50 1200,0 1200,370 0,420" fill="#f7931e"/>
    <polygon points="0,50 520,28 300,420 0,420" fill="#f9a233" opacity=".6"/>
    <polygon points="700,12 1200,0 1200,220" fill="#f07a12" opacity=".5"/>
  </svg>
  <h2 class="abs thin">Fun</h2>
  <div class="abs rule"></div>
  <p class="abs" style="top:184px">Forget what you know - <b>Lumvra makes it fun to quit.</b> The balance between your goal and each day with a simple and <b>gamified approach</b> for managing small changes.</p>
  <p class="abs" style="top:270px">Lumvra gives you the opportunity to play an <b>active role</b> in helping yourself &amp; <b>others</b> on a path where the experience turns from a lonely effort into a team game. That's right, we converted the quitting process into a social game.</p>
  <div class="tablet abs" role="img" aria-label="Tablet showing the Lumvra social feed"></div>
</section>

<section class="inspire">
  <svg class="abs" style="left:0;top:0" width="1200" height="400" viewBox="0 0 1200 400" aria-hidden="true">
    <polygon points="0,20 1200,0 1200,390 0,400" fill="#fbb829"/>
    <polygon points="0,20 420,13 180,400 0,400" fill="#fdc94a" opacity=".7"/>
    <polygon points="820,6 1200,0 1200,390 980,392" fill="#f9a825" opacity=".5"/>
  </svg>
  <div class="tablet abs" role="img" aria-label="Tablet showing an inspiring Lumvra profile screen"></div>
  <h2 class="abs thin">Inspire</h2>
  <div class="abs rule"></div>
  <p class="abs" style="top:170px">One of the most important factors for successful quitting is the ability to <b>stay inspired</b> during the process.</p>
  <p class="abs" style="top:240px">That's why we designed Lumvra as a platform where you can inspire and be inspired by a supportive network of awesome Lumvra ninjas!</p>
</section>

<section class="achieve">
  <h2 class="abs" style="font-family:'Raleway',sans-serif">Achieve</h2>
  <div class="abs rule"></div>
  <p class="abs intro" style="top:140px">Lumvra is built as a <b>pyramid of relationships</b> that makes use of the <b>Social Cognitive Theory</b>, to provide a powerful network of positive reinforcement.</p>
  <p class="abs intro" style="top:196px">The bigger you make it the stronger you get.</p>
  <div class="device phone" role="img" aria-label="Smartphone showing the Lumvra progress screen"></div>
  <div class="point" style="left:70px;top:300px"><p>Lumvra is built as a pyramid of relationships that makes use of the Social Cognitive Theory</p><span class="dot"><svg width="26" height="26"><circle cx="13" cy="13" r="9" fill="#fff"/></svg></span></div>
  <div class="point" style="left:70px;top:420px"><p>Lumvra is built as a pyramid of relationships that makes use of the Social Cognitive Theory</p><span class="dot"><svg width="26" height="26"><rect x="4" y="9" width="18" height="8" rx="4" fill="#fff"/></svg></span></div>
  <div class="point right" style="left:760px;top:300px"><p>Lumvra is built as a pyramid of relationships that makes use of the Social Cognitive Theory</p><span class="dot"><svg width="26" height="26"><path d="M6 4h14v6a7 7 0 0 1-14 0z M11 17h4v4h4v2H7v-2h4z" fill="#fff"/></svg></span></div>
  <div class="point right" style="left:760px;top:420px"><p>Lumvra is built as a pyramid of relationships that makes use of the Social Cognitive Theory</p><span class="dot"><svg width="26" height="26"><polygon points="13,3 24,23 2,23" fill="none" stroke="#fff" stroke-width="2.5"/></svg></span></div>
</section>

<section class="soon">
  <div class="soon-bg" role="img" aria-label="Dark moody backdrop with warm brown light"></div>
  <svg class="abs" style="left:0;top:0" width="1200" height="60" viewBox="0 0 1200 60" aria-hidden="true">
    <polygon points="0,0 1200,0 600,40" fill="#ffffff"/>
  </svg>
  <h2 class="abs">Coming Soon</h2>
  <div class="device phone" role="img" aria-label="Smartphone showing the Lumvra app with earphones beside it"></div>
  <svg class="abs" style="left:110px;top:300px" width="70" height="30" viewBox="0 0 70 30" aria-hidden="true"><line x1="4" y1="15" x2="68" y2="15" stroke="#fff" stroke-width="3"/><polyline points="18,3 4,15 18,27" fill="none" stroke="#fff" stroke-width="3"/></svg>
  <svg class="abs" style="left:1020px;top:300px" width="70" height="30" viewBox="0 0 70 30" aria-hidden="true"><line x1="2" y1="15" x2="66" y2="15" stroke="#fbb829" stroke-width="3"/><polyline points="52,3 66,15 52,27" fill="none" stroke="#fbb829" stroke-width="3"/></svg>
</section>

<section class="stores">
  <div class="store s1"><span class="mark"></span><small>Download on the</small><strong>APPSHELF</strong></div>
  <div class="store s2"><span class="mark"></span><small>Get it on</small><strong>PLAYMART</strong></div>
  <div class="store s3"><span class="mark"></span><small>Get it on</small><strong>PANEMARKET</strong></div>
</section>

<section class="desktop">
  <div class="abs ghost">DESKTOP?</div>
  <h2 class="abs">On desktop, on your mobile, on your laptop, online, well, not lovely ?</h2>
  <p class="abs">Lorem Ipsum is simply dummy text of the printing and typesetting industry. Lorem Ipsum has been the industry's standard dummy text ever since the 1500s, when an unknown printer took a galley of type and scrambled it to make a type specimen book.</p>
  <div class="abs icons"><span></span><span></span><span></span><span></span></div>
  <div class="abs devices" role="img" aria-label="Desktop, laptop, tablet and phone all showing the Lumvra app"></div>
</section>

<section class="strip" role="img" aria-label="Row of lifestyle photos: a market stall, a bicycle, friends outdoors, a city street, a meal and a coffee cup">
  <div style="background:linear-gradient(160deg,#6e8b4a,#c9a25a)"></div>
  <div style="background:linear-gradient(160deg,#8fb6c9,#c84a3a)"></div>
  <div style="background:linear-gradient(160deg,#d9c9a8,#7d6a55)"></div>
  <div style="background:linear-gradient(160deg,#b0b7bd,#5a5f66)"></div>
  <div style="background:linear-gradient(160deg,#e8ddc8,#9a6b3c)"></div>
  <div style="background:linear-gradient(160deg,#4a3628,#c49a6c)"></div>
</section>

<footer class="site-footer">
  <h2 class="abs">Subscribe below for the beta release and updates.</h2>
  <div class="abs email">Enter your e-mail address
    <span class="go"><svg width="20" height="14" viewBox="0 0 20 14"><rect x="1" y="1" width="18" height="12" fill="none" stroke="#fff" stroke-width="2"/><polyline points="1,1 10,8 19,1" fill="none" stroke="#fff" stroke-width="2"/></svg></span>
  </div>
  <div class="abs brand">Lumvra</div>
  <div class="abs counts"><span><i></i>500</span><span><i></i>25</span><span><i></i>400</span></div>
  <div class="abs legal"><span>Home</span><span>|</span><span>T&amp;Cs</span><span>|</span><span>Privacy Policy</span></div>
  <div class="abs copyright">© 2016 Lumvra Ltd. All Rights Reserved</div>
  <div class="abs footer-stores">
    <div style="background:var(--charcoal)"><span class="mark"></span><span><small>Available on the</small><strong>APPSHELF</strong></span></div>
    <div style="background:var(--yellow)"><span class="mark"></span><span><small>Get it on</small><strong>PLAYMART</strong></span></div>
    <div style="background:var(--blue)"><span class="mark"></span><span><small>Get it on</small><strong>PANEMARKET</strong></span></div>
  </div>
</footer>

</body>
</html>
```